Redesign of the UI of a customer service platform

To improve the user experience of our customers, we need a new design for our agent interface of our customer service platform (helpora).
The focus will be on the dashboard and the inbox screens (see attached) along with the common UI elements (Buttons, menu, fonts, forms...)
We want a simple and distinctive design

Target Market(s)

Worldwide

Industry/Entity Type

It Service

Number of Pages Required

3 page

Font styles to use
Sans Serif

Requirements
Must have
• New Onboarding page: this is a new page that is shown to user the first time they login to the platform. This will replace the current onboarding screen (setup SMS, Setup widget...etc)
• Dashboard page: to access important information and activate services (see screenshot from current site)
• Inbox page: to manage all the interactions with customers. (see screenshot from current site)
• UI elements (buttons, menus, forms, tables, fonts, color palette)

```html
<!DOCTYPE html>
<html lang="en">
<head>
<meta charset="utf-8">
<title>Helpora — Dashboard</title>
<link href="https://fonts.googleapis.com/css2?family=Open+Sans:wght@400;600&display=swap" rel="stylesheet">
<style>
:root{
  --orange:#f4511e;
  --red:#e8261c;
  --yellow:#f5bd14;
  --green:#3cb72c;
  --page:#f2f2f2;
  --white:#ffffff;
  --line:#e3e3e3;
  --icon:#a9a9a9;
  --text:#3a3a3a;
  --muted:#8c8c8c;
}
*{box-sizing:border-box;margin:0;padding:0}
html,body{width:1200px;height:831px;overflow:hidden}
body{background:var(--page);font-family:"Open Sans",sans-serif;color:var(--text);position:relative}
.topbar{position:absolute;left:0;top:0;width:1200px;height:83px;background:var(--white);display:flex}
.brand{width:83px;height:83px;background:var(--orange);color:var(--white);display:flex;align-items:center;justify-content:center;font-size:13px;font-weight:600}
.nav{display:flex}
.nav-item{width:84px;height:83px;border-right:1px solid #ececec;display:flex;flex-direction:column;align-items:center;justify-content:center;gap:7px;color:var(--muted);font-size:13px;position:relative}
.nav-item svg{width:26px;height:26px}
.badge{position:absolute;top:17px;left:50px;width:22px;height:22px;border-radius:50%;color:#fff;font-size:12px;display:flex;align-items:center;justify-content:center}
.badge.red{background:var(--red)}
.badge.yellow{background:var(--yellow)}
.avatar{position:absolute;right:15px;top:14px;width:55px;height:55px;border-radius:50%;background:linear-gradient(160deg,#cfd6dc,#8b98a3);border:2px solid #eee}
.online{position:absolute;right:56px;top:14px;width:15px;height:15px;border-radius:50%;background:var(--green);border:2px solid #fff}
.video{position:absolute;left:18px;top:102px;width:894px;height:499px;overflow:hidden}
.video-photo{position:absolute;inset:0;background:radial-gradient(ellipse at 65% 40%,#7a5a45 0%,#4b3c33 45%,#2b2420 100%)}
.play{position:absolute;left:398px;top:179px;width:98px;height:98px;border-radius:50%;background:rgba(230,230,230,.85);border:6px solid #fff;display:flex;align-items:center;justify-content:center}
.video-title{position:absolute;left:0;width:100%;top:294px;text-align:center;color:#fff;font-size:20px}
.controls{position:absolute;left:28px;top:453px;display:flex;align-items:center;gap:8px;color:#fff;font-size:12px}
.track{position:absolute;left:77px;top:464px;width:790px;height:3px;background:#ddd}
.track span{display:block;width:399px;height:3px;background:var(--orange)}
.plan{position:absolute;left:940px;top:102px;width:242px;height:499px;background:var(--white);padding:18px 21px}
.plan h2{font-size:20px;font-weight:400;display:flex;align-items:center;gap:8px}
.tag{background:var(--orange);color:#fff;font-size:10px;padding:2px 5px;border-radius:2px;font-weight:600}
.plan p{font-size:12px;color:var(--muted);margin-top:3px}
.limits{margin-top:23px;border:1px solid var(--line)}
.limit{height:114px;border-bottom:1px solid var(--line);position:relative;display:flex;flex-direction:column;align-items:center;justify-content:center}
.limit:last-child{border-bottom:none}
.limit svg{width:34px;height:34px;margin-bottom:6px}
.limit strong{font-weight:400;font-size:16px}
.limit small{font-size:12px;color:var(--muted)}
.count{position:absolute;right:10px;top:10px;background:var(--orange);color:#fff;font-size:10px;padding:1px 7px;border-radius:2px}
.buy{display:block;margin:24px auto 0;width:83px;height:27px;background:var(--green);color:#fff;font-size:12px;font-weight:600;border:none;font-family:inherit}
.addons-title{position:absolute;left:18px;top:624px;font-size:19px;font-weight:400}
.addons{position:absolute;left:18px;top:672px;display:flex;gap:14px}
.addon{width:222px;height:83px;background:var(--white);border:1px solid var(--line);display:flex;position:relative}
.addon-icon{width:74px;border-right:1px solid var(--line);display:flex;align-items:center;justify-content:center}
.addon-icon svg{width:28px;height:28px}
.addon-body{padding:20px 0 0 18px}
.addon-body h3{font-size:16px;font-weight:400}
.addon-body a{font-size:11px;color:var(--orange);text-decoration:none}
.check{position:absolute;right:6px;top:6px}
</style>
</head>
<body>
<header class="topbar">
  <div class="brand">helpora</div>
  <nav class="nav">
    <div class="nav-item"><svg viewBox="0 0 26 26"><path d="M3 14h6l2 3h4l2-3h6v8H3z" fill="var(--icon)"/><path d="M13 3v9M9 8l4 4 4-4" stroke="var(--icon)" stroke-width="2" fill="none"/></svg>Inbox<span class="badge red">4</span></div>
    <div class="nav-item"><svg viewBox="0 0 26 26"><rect x="4" y="3" width="16" height="20" fill="none" stroke="var(--icon)" stroke-width="2"/><path d="M8 8h8M8 12h8M8 16h5" stroke="var(--icon)" stroke-width="2"/></svg>Tasks<span class="badge yellow">1</span></div>
    <div class="nav-item"><svg viewBox="0 0 26 26"><circle cx="13" cy="9" r="5" fill="var(--icon)"/><path d="M4 24c0-6 4-9 9-9s9 3 9 9z" fill="var(--icon)"/></svg>Customers</div>
    <div class="nav-item"><svg viewBox="0 0 26 26"><path d="M2 5l22 8-22 8 4-8z" fill="none" stroke="var(--icon)" stroke-width="2" stroke-linejoin="round"/><path d="M6 13h18" stroke="var(--icon)" stroke-width="2"/></svg>Campaigns</div>
    <div class="nav-item"><svg viewBox="0 0 26 26"><text x="13" y="21" text-anchor="middle" font-size="22" fill="var(--icon)" font-family="Open Sans,sans-serif">$</text></svg>Payments</div>
    <div class="nav-item"><svg viewBox="0 0 26 26"><path d="M4 4v19M10 10v13M16 6v17M22 14v9" stroke="var(--icon)" stroke-width="3"/></svg>Reports</div>
    <div class="nav-item"><svg viewBox="0 0 26 26"><circle cx="13" cy="13" r="8" fill="none" stroke="var(--icon)" stroke-width="5" stroke-dasharray="3 2.3"/><circle cx="13" cy="13" r="6" fill="none" stroke="var(--icon)" stroke-width="3"/></svg>Settings</div>
  </nav>
  <div class="avatar" role="img" aria-label="Agent profile photo"></div>
  <span class="online"></span>
</header>

<section class="video">
  <div class="video-photo" role="img" aria-label="Team working together over documents at a desk"></div>
  <div class="play"><svg width="28" height="32" viewBox="0 0 28 32"><path d="M2 1l25 15L2 31z" fill="var(--orange)"/></svg></div>
  <div class="video-title">Get Started</div>
  <div class="controls"><svg width="10" height="12" viewBox="0 0 10 12"><path d="M0 0l10 6-10 6z" fill="#fff"/></svg>0:00</div>
  <div class="track"><span></span></div>
</section>

<aside class="plan">
  <h2>Plan <span class="tag">FREE</span></h2>
  <p>Your trial period ends in 14 days</p>
  <div class="limits">
    <div class="limit"><span class="count">1/3</span>
      <svg viewBox="0 0 34 34"><circle cx="17" cy="10" r="5" fill="var(--icon)"/><circle cx="8" cy="13" r="4" fill="var(--icon)"/><circle cx="26" cy="13" r="4" fill="var(--icon)"/><path d="M9 28c0-6 3-10 8-10s8 4 8 10z M1 26c0-5 3-8 7-8 2 0 3 1 3 1-2 2-3 5-3 7z M33 26c0-5-3-8-7-8-2 0-3 1-3 1 2 2 3 5 3 7z" fill="var(--icon)"/></svg>
      <strong>Agents</strong><small>Up to 3</small></div>
    <div class="limit"><span class="count">1/3</span>
      <svg viewBox="0 0 34 34"><path d="M13 9V6h8v3" fill="none" stroke="var(--icon)" stroke-width="2"/><rect x="2" y="9" width="30" height="20" rx="2" fill="var(--icon)"/><rect x="15" y="16" width="4" height="4" fill="#fff"/></svg>
      <strong>Departments</strong><small>Up to 3</small></div>
    <div class="limit"><span class="count">1/3</span>
      <svg viewBox="0 0 34 34"><path d="M8 3l5 7-3 3c2 4 5 8 10 11l3-3 7 5-4 5C15 30 4 19 3 8z" fill="var(--icon)"/></svg>
      <strong>Phones</strong><small>Up to 1</small></div>
  </div>
  <button class="buy">BUY NOW</button>
</aside>

<h2 class="addons-title">Select Your Add-ons</h2>
<section class="addons">
  <div class="addon"><div class="addon-icon"><svg viewBox="0 0 28 28"><rect x="2" y="5" width="24" height="15" fill="none" stroke="var(--icon)" stroke-width="2"/><rect x="5" y="8" width="18" height="9" fill="var(--icon)"/><path d="M10 24h8M14 20v4" stroke="var(--icon)" stroke-width="2"/></svg></div><div class="addon-body"><h3>Campaigns</h3><a href="#">WATCH VIDEO</a></div></div>
  <div class="addon"><div class="addon-icon"><svg viewBox="0 0 28 28"><circle cx="14" cy="14" r="8" fill="var(--icon)"/></svg></div><div class="addon-body"><h3>Chatwire</h3><a href="#">WATCH VIDEO</a></div></div>
  <div class="addon"><div class="addon-icon"><svg viewBox="0 0 28 28"><path d="M14 3C7 3 2 8 2 13c0 3 1 5 3 7l-1 5 5-3c2 1 3 1 5 1 7 0 12-5 12-10S21 3 14 3z" fill="var(--icon)"/><path d="M9 11h10M9 14h10M9 17h7" stroke="#fff" stroke-width="1.5"/></svg></div><div class="addon-body"><h3>SMS</h3><a href="#">WATCH VIDEO</a></div>
    <svg class="check" width="22" height="22" viewBox="0 0 22 22"><circle cx="11" cy="11" r="10" fill="var(--green)"/><path d="M6 11l3.5 3.5L16 8" stroke="#fff" stroke-width="2.4" fill="none"/></svg></div>
  <div class="addon"><div class="addon-icon"><svg viewBox="0 0 28 28"><rect x="7" y="7" width="14" height="14" fill="var(--icon)"/></svg></div><div class="addon-body"><h3>Wirepost</h3><a href="#">WATCH VIDEO</a></div></div>
  <div class="addon"><div class="addon-icon"><svg viewBox="0 0 28 28"><text x="14" y="23" text-anchor="middle" font-size="26" fill="var(--icon)" font-family="Open Sans,sans-serif" font-weight="600">$</text></svg></div><div class="addon-body"><h3>Payment</h3><a href="#">WATCH VIDEO</a></div></div>
</section>
</body>
</html>
```